Flyer Promoting Dental Benefit Program

I want to promote a dental benefit program to my patients that do not have dental insurance. This flyer would be posted in our waiting room and where people make payments. The goal would be to get those interested to request more information and enroll in the program. I have a card that will be issued that has a logo. Theflyer and card should feel congruent. I've uploaded a file with a copy of that card.
The plan costs $290/person. It includes 2 cleanings, exams, and x-rays. It also includes a 20% discount off of our standard fees. The plan or membership lasts for one year. It is only available to those without insurance. It is also important to let people know that this is not insurance (some kind of a disclaimer).
Updates
This plan is only available to patients at my office. The contact information is: Harborview Dental, 2718 West 4600 North Suite 209, Salt Lake City, Utah 84157. (801) 563-9071. info@harborviewdental-example.com. It is not necessary to include contact information as this flyer will be used as in-office promotion.
Target Market(s)
Those without dental insurance, but have resources to afford dental care.
Industry/Entity Type
Insurance
Look and feel
Each slider illustrates characteristics of the customer's brand and the style your logo design should communicate.

```html
<!DOCTYPE html>
<html lang="en">
<head>
<meta charset="utf-8">
<title>Harborview Dental – Care Plan</title>
<link rel="stylesheet" href="https://fonts.googleapis.com/css2?family=Alegreya:wght@400&family=Source+Sans+3:wght@400;600&family=Arimo:wght@400&display=swap">
<style>
  :root {
    --leaf-green: #78b357;
    --frame-green: #6cb24a;
    --coral: #f07150;
    --ink: #1d1d1d;
    --muted-ink: #333333;
    --paper: #ffffff;
    --stage: #ececec;
    --photo-family: linear-gradient(160deg, #e9ecef 0%, #d8c2ae 55%, #b8a595 100%);
    --photo-playful: linear-gradient(180deg, #f3f4f6 0%, #9c6b4f 60%, #6a4a38 100%);
    --photo-seniors: linear-gradient(160deg, #8da36f 0%, #d9cfc6 55%, #ece9e5 100%);
  }
  * { box-sizing: border-box; margin: 0; padding: 0; }
  html, body { width: 898px; height: 1200px; overflow: hidden; background: var(--stage); }
  .flyer {
    position: relative; width: 898px; height: 1200px;
    background: var(--paper); color: var(--ink);
    font-family: "Source Sans 3", Arial, sans-serif;
  }
  .tagline {
    position: absolute; left: 96px; top: 24px; width: 270px;
    font-family: "Arimo", Arial, sans-serif; font-size: 21px; line-height: 32px;
    text-align: center;
  }
  .headline-leaf {
    position: absolute; left: 76px; top: 105px; width: 322px; height: 312px;
    background: var(--leaf-green);
    border-radius: 0 90px 0 90px;
    display: flex; align-items: center; padding-left: 16px;
  }
  .headline-leaf h1 {
    font-family: "Alegreya", Georgia, serif; font-weight: 400;
    font-size: 52px; line-height: 64px; color: var(--paper);
  }
  .photo { position: absolute; border: 4px solid var(--frame-green); }
  .photo--family {
    left: 412px; top: 45px; width: 384px; height: 372px;
    border-radius: 90px 0 90px 0; background: var(--photo-family);
  }
  .photo--playful {
    left: 158px; top: 432px; width: 240px; height: 235px;
    border-radius: 60px 0 60px 0; background: var(--photo-playful);
  }
  .photo--seniors {
    left: 419px; top: 949px; width: 302px; height: 186px;
    border-radius: 14px; background: var(--photo-seniors);
  }
  .discount {
    position: absolute; left: 419px; top: 430px;
    font-family: "Alegreya", Georgia, serif; font-size: 40px; line-height: 47px;
    color: var(--coral); text-transform: uppercase;
  }
  .discount .rate { color: var(--ink); font-size: 46px; }
  .plan-name {
    position: absolute; left: 560px; top: 662px; width: 250px;
    font-family: "Source Sans 3", Arial, sans-serif; font-weight: 600;
    font-size: 26px; line-height: 32px; color: var(--muted-ink);
    text-align: right;
  }
  .plan-details {
    position: absolute; left: 116px; top: 720px; list-style: none;
    font-size: 29px; line-height: 57px;
  }
  .plan-details li { display: flex; align-items: center; }
  .plan-details li::before {
    content: ""; width: 11px; height: 11px; border-radius: 50%;
    background: var(--coral); margin-right: 22px; flex: none;
  }
  .plan-details .price { color: var(--coral); font-size: 34px; }
  .practice-name {
    position: absolute; left: 99px; top: 990px; width: 290px;
    font-family: "Alegreya", Georgia, serif; font-size: 46px; line-height: 54px;
    color: var(--muted-ink);
  }
  .disclaimer {
    position: absolute; left: 0; right: 0; top: 1166px; text-align: center;
    font-family: "Arimo", Arial, sans-serif; font-size: 14px; padding-left: 100px;
  }
</style>
</head>
<body>
  <main class="flyer">
    <p class="tagline">Together with Kindness, Knowledge &amp;Skill.....</p>

    <div class="headline-leaf">
      <h1>We Provide Excellent Dental Care</h1>
    </div>

    <div class="photo photo--family" role="img" aria-label="Photo of a smiling family of four"></div>
    <div class="photo photo--playful" role="img" aria-label="Photo of a laughing family playing together"></div>

    <p class="discount">It also<br>includes a<br><span class="rate">20%</span> discount<br>of our standard<br>fees</p>

    <p class="plan-name">Harborview Care Plan</p>

    <ul class="plan-details">
      <li><span>The plan costs <span class="price">$290</span>/person</span></li>
      <li>It includes 2 cleanings, exams, and x-rays</li>
      <li>The plan or membership lasts for one year</li>
      <li>It is only available to those without insurance</li>
    </ul>

    <p class="practice-name">Harborview Dental</p>

    <div class="photo photo--seniors" role="img" aria-label="Photo of a smiling senior couple"></div>

    <p class="disclaimer">Disclaimer:&nbsp; It is also important to let people know that this is not insurance</p>
  </main>
</body>
</html>
```